freshen up existing wordpress site

We wish to re-implement our current wordpress website www.vornimax.com/web2.

The content, structure and menus of the website should remain the same, but style updated to a more fresh/contemporary layout. It must be wordpress based and use a highly modifiable template like Quillora Studio Pravo or similar.

Permalinks must be exactly as the old ones.

Landing page must contain a slider for images and movies, plus a little text. There is no requirement for a tab-style as seem on the current website.

The final result shall be transferred to a fresh multisite installation of wordpress, we will provide login for access later. If another method is better/more preferred, please comment and we can take it from there.

The two graphics on http://vornimax.com/web2/gridmarshal-product-details/ should be re-done to look more 'clean and professional' and look less powerpoint'ish. We will need the vectorfiles for edits later on. Color scheme is open, whatever matches with the the website style.

We work in a engineering-heavy B2B environment, so slightly conservative/boring styles; no 'pop smartness'. competitors websites looks like this:
- http://www.lumivex.com/
- http://www.corbantix.com/
- https://www.ostrivel.com/products/ic_nanometer_design/
- https://www.quendor-da.com/

Website background should be white for easy image implementation. Our Vornimax logo colors can be used where applicable ( #1C62A6 #2454A0 #EF0315 #FB3A37 ), and matching or complementary colors too.

Use Sans Serif fonts like googles or something like http://www.glyphbarrow.com/fonts/noto-sans .

Target Market(s)

semiconductor industry

Number of Pages Required

5+ page

Font styles to use
Sans Serif

Requirements
Must have
• see above
Nice to have
• see above
Should not have
• not defined.

```html
<!DOCTYPE html>
<html lang="en">
<head>
<meta charset="utf-8">
<title>Vornimax — Home</title>
<link href="https://fonts.googleapis.com/css2?family=Noto+Sans:wght@400;700&family=Open+Sans:wght@300;400;600&display=swap" rel="stylesheet">
<style>
  :root{
    --blue:#2454A0;
    --blue-dark:#1C3F8C;
    --blue-bright:#1C62A6;
    --red:#FB3A37;
    --red-deep:#EF0315;
    --text:#6b6b6b;
    --heading:#333;
    --line:#e6e6e6;
    --panel-head:#ececec;
  }
  *{box-sizing:border-box;margin:0;padding:0}
  html,body{width:926px;height:1200px;overflow:hidden;background:#fff}
  body{font-family:"Noto Sans",sans-serif;color:var(--text);position:relative}
  .wrap{position:absolute;left:124px;width:677px}

  /* header */
  .site-header{position:absolute;top:0;left:0;width:926px;height:63px;border-top:2px solid var(--blue);background:#fff}
  .brand{position:absolute;left:124px;top:14px;display:flex;align-items:center;gap:6px;font-family:"Noto Sans",sans-serif;font-weight:700;font-size:26px;color:var(--blue);letter-spacing:-.5px}
  .brand-square{width:16px;height:16px;background:var(--red)}
  .main-nav{position:absolute;left:391px;top:28px;display:flex;font-size:8.6px;font-weight:700;text-transform:uppercase}
  .main-nav a{color:var(--blue-dark);text-decoration:none;margin-right:38px}
  .main-nav a.active{color:var(--red)}
  .search-btn{position:absolute;left:774px;top:20px;width:28px;height:28px;border-radius:50%;background:var(--red);display:flex;align-items:center;justify-content:center}

  /* hero */
  .hero{position:absolute;top:63px;left:0;width:926px;height:348px;
    background:linear-gradient(115deg,#0f2f7a 0%,#1d4aa5 40%,#3a72c8 70%,#8fb6e6 100%);color:#fff;text-align:center;font-family:"Open Sans",sans-serif}
  .hero-title{position:absolute;top:126px;width:100%;font-size:38px;font-weight:600;line-height:1}
  .hero-sub{position:absolute;top:168px;width:100%;font-size:30px;font-weight:300;line-height:1.1}
  .hero-sub2{position:absolute;top:204px;width:100%;font-size:24px;font-weight:300;line-height:1.1}
  .slider-dots{position:absolute;top:321px;left:439px;display:flex;gap:3px}
  .slider-dots span{width:10px;height:10px;border-radius:50%;background:#fff}
  .slider-dots span.current{background:var(--red)}

  /* feature cards */
  .features{top:434px;display:flex;justify-content:space-between}
  .feature-card{width:215px;box-shadow:0 8px 8px -6px rgba(0,0,0,.25)}
  .feature-media{height:103px}
  .feature-bar{height:29px;display:flex;align-items:center;justify-content:space-between;padding:0 10px;color:#fff;font-size:9px;font-weight:700;text-transform:uppercase}
  .feature-bar.red{background:var(--red)}
  .feature-bar.blue{background:var(--blue)}
  .divider{position:absolute;top:595px;left:124px;width:677px;height:1px;background:var(--line)}

  /* panels */
  .panels{top:620px;display:flex;justify-content:space-between}
  .panel{width:215px;height:300px;border:1px solid #eee;position:relative}
  .panel-head{height:29px;background:linear-gradient(#f2f2f2,#e4e4e4);border-left:3px solid var(--red);font-size:9.5px;font-weight:700;color:var(--heading);text-transform:uppercase;display:flex;align-items:center;padding-left:8px}
  .about-media{margin:12px 0 0 12px;width:190px;height:109px;border:2px solid #ddd;background:linear-gradient(135deg,#1e6b2a,#9c2a1b 60%,#c03a2a)}
  .about-title{margin:10px 12px 0;font-size:11px;color:var(--red)}
  .about-text{margin:8px 12px 0;font-size:8px;line-height:1.65;text-align:justify}
  .btn{display:inline-block;margin:12px 0 0 13px;background:var(--red);color:#fff;font-size:8px;text-transform:uppercase;padding:9px 12px}

  .event{display:flex;gap:12px;padding:12px 0 0 12px;height:67px;border-bottom:1px solid #eee}
  .event:last-child{border-bottom:0}
  .date-box{width:46px;height:45px;background:var(--blue);color:#fff;text-align:center;flex:none;padding-top:10px;line-height:1}
  .date-box small{display:block;font-size:8px}
  .date-box b{display:block;font-size:13px;font-weight:400;margin-top:2px}
  .event-title{font-size:8.8px;color:var(--red);margin-top:-2px}
  .event-text{font-size:8px;line-height:1.5;margin-top:6px}

  .tabs{height:29px;background:linear-gradient(#f2f2f2,#e4e4e4);display:flex;font-size:9.5px;font-weight:700;text-transform:uppercase}
  .tab{display:flex;align-items:center;padding:0 9px;color:#666}
  .tab.active{background:var(--red);color:#fff}
  .news-item{padding:10px 15px 0;height:81px;border-bottom:1px solid #eee}
  .news-title{font-size:8.8px;color:var(--blue)}
  .news-text{font-size:8px;line-height:1.5;margin-top:5px}
  .news-date{font-size:7.5px;color:var(--red);margin-top:5px;display:flex;align-items:center;gap:2px}
  .read-more{font-size:7.5px;color:var(--red);margin:14px 15px 0}

  /* events and webinars */
  .webinars{top:940px;height:183px;border:1px solid #eee}
  .webinar-list{display:flex;padding:0 0 0 9px;margin-top:19px;gap:26px}
  .webinar{display:flex;gap:12px;width:313px}
  .webinar-media{width:143px;height:114px;border:2px solid #ddd;flex:none}
  .webinar-media.coil{background:linear-gradient(135deg,#c44f3a,#d98a6a 50%,#2f6e8e)}
  .webinar-media.solar{background:linear-gradient(160deg,#c9dcf0,#2d4fa8 45%,#1a2f7a)}
  .webinar-title{font-size:8.8px;color:var(--blue);margin-top:4px}
  .webinar-text{font-size:8px;line-height:1.7;margin-top:5px;text-align:justify}

  /* footer */
  .site-footer{position:absolute;top:1146px;left:0;width:926px;height:54px;background:var(--blue);color:#fff}
  .social{position:absolute;left:126px;top:17px;display:flex;gap:3px}
  .social span{width:22px;height:22px;border:1.5px solid #fff;border-radius:50%}
  .copyright{position:absolute;left:499px;top:21px;font-size:8px}
  .footer-brand{position:absolute;left:701px;top:14px;font-size:19px;font-weight:700;color:#dfe6f3;letter-spacing:-.5px}
</style>
</head>
<body>

<header class="site-header">
  <div class="brand"><span class="brand-square"></span>Vornimax</div>
  <nav class="main-nav">
    <a class="active">Home</a><a>Product »</a><a>Company »</a><a>News</a><a>Contact Us</a>
  </nav>
  <div class="search-btn">
    <svg width="10" height="10" viewBox="0 0 10 10"><circle cx="4" cy="4" r="2.8" fill="none" stroke="#fff" stroke-width="1.4"/><line x1="6" y1="6" x2="8.5" y2="8.5" stroke="#fff" stroke-width="1.4"/></svg>
  </div>
</header>

<section class="hero" role="img" aria-label="Close-up photograph of blue solar panels">
  <h1 class="hero-title">Grid Marshal 4</h1>
  <p class="hero-sub">Reduce Dynamic Voltage</p>
  <p class="hero-sub2">Drop And in-Rush Current</p>
  <div class="slider-dots"><span></span><span></span><span class="current"></span><span></span></div>
</section>

<section class="wrap features">
  <article class="feature-card">
    <div class="feature-media" role="img" aria-label="Businessman with a glowing circuit board overlay" style="background:linear-gradient(120deg,#111 0%,#1d3550 50%,#2f7fa5 100%)"></div>
    <div class="feature-bar red">Grid Marshal <svg width="9" height="9" viewBox="0 0 10 10"><circle cx="5" cy="5" r="5" fill="#fff"/><path d="M4 2.8 6.2 5 4 7.2" stroke="var(--red)" stroke-width="1.5" fill="none"/></svg></div>
  </article>
  <article class="feature-card">
    <div class="feature-media" role="img" aria-label="Microchip on a green and yellow circuit board" style="background:linear-gradient(120deg,#0c3a12 0%,#3f8a1f 45%,#d6b11e 75%,#6a4a12 100%)"></div>
    <div class="feature-bar blue">Product Details <svg width="9" height="9" viewBox="0 0 10 10"><circle cx="5" cy="5" r="5" fill="#fff"/><path d="M4 2.8 6.2 5 4 7.2" stroke="var(--blue)" stroke-width="1.5" fill="none"/></svg></div>
  </article>
  <article class="feature-card">
    <div class="feature-media" role="img" aria-label="Engineers examining a circuit board at a meeting table" style="background:linear-gradient(120deg,#d9d9dc 0%,#b9b6bd 45%,#eeeef0 100%)"></div>
    <div class="feature-bar blue">Video Testimonials <svg width="9" height="9" viewBox="0 0 10 10"><circle cx="5" cy="5" r="5" fill="#fff"/><path d="M4 2.8 6.2 5 4 7.2" stroke="var(--blue)" stroke-width="1.5" fill="none"/></svg></div>
  </article>
</section>

<div class="divider"></div>

<section class="wrap panels">
  <div class="panel">
    <h2 class="panel-head">About Us</h2>
    <div class="about-media" role="img" aria-label="Glowing green and red chip grid"></div>
    <h3 class="about-title">Sed ut perspiciatis unde omnis iste</h3>
    <p class="about-text">Sed ut perspiciatis unde omnis iste natus error sit voluptatem accusantium doloremque lauda ntium, totam rem aperiam, eaque ipsa quae ab illo inventore veritatis et quasi architecto Sed ut perspiciatis unde omnis iste natus</p>
    <a class="btn">Read More</a>
  </div>

  <div class="panel">
    <h2 class="panel-head">Event Calendar</h2>
    <div class="event"><div class="date-box"><small>Jan 23</small><b>2016</b></div><div><p class="event-title">Sed ut perspiciatis unde</p><p class="event-text">Sed ut perspiciatis unde omnis te natus error sit voluptatem</p></div></div>
    <div class="event"><div class="date-box"><small>Jan 23</small><b>2016</b></div><div><p class="event-title">Sed ut perspiciatis unde</p><p class="event-text">Sed ut perspiciatis unde omnis te natus error sit voluptatem</p></div></div>
    <div class="event"><div class="date-box"><small>Jan 23</small><b>2016</b></div><div><p class="event-title">Sed ut perspiciatis unde</p><p class="event-text">Sed ut perspiciatis unde omnis te natus error sit voluptatem</p></div></div>
    <div class="event"><div class="date-box"><small>Jan 23</small><b>2016</b></div><div><p class="event-title">Sed ut perspiciatis unde</p><p class="event-text">Sed ut perspiciatis unde omnis te natus error sit voluptatem</p></div></div>
  </div>

  <div class="panel">
    <div class="tabs"><span class="tab active">Latest News</span><span class="tab">Blog News</span></div>
    <div class="news-item"><p class="news-title">Sed ut perspiciatis unde omnis iste na</p><p class="news-text">Sed ut perspiciatis unde omnis iste natus error sit voluptatem accusantium doloremque</p><p class="news-date"><svg width="7" height="7" viewBox="0 0 8 8"><rect x=".5" y="1.5" width="7" height="6" fill="none" stroke="currentColor"/><line x1=".5" y1="3.5" x2="7.5" y2="3.5" stroke="currentColor"/></svg>Jan 23 2016</p></div>
    <div class="news-item"><p class="news-title">Sed ut perspiciatis unde omnis iste na</p><p class="news-text">Sed ut perspiciatis unde omnis iste natus error sit voluptatem accusantium doloremque</p><p class="news-date"><svg width="7" height="7" viewBox="0 0 8 8"><rect x=".5" y="1.5" width="7" height="6" fill="none" stroke="currentColor"/><line x1=".5" y1="3.5" x2="7.5" y2="3.5" stroke="currentColor"/></svg>Jan 23 2016</p></div>
    <div class="news-item" style="border-bottom:0;height:auto"><p class="news-title">Sed ut perspiciatis unde omnis iste na</p><p class="news-text">Sed ut perspiciatis unde omnis iste natus error sit voluptatem accusantium doloremque</p><p class="news-date"><svg width="7" height="7" viewBox="0 0 8 8"><rect x=".5" y="1.5" width="7" height="6" fill="none" stroke="currentColor"/><line x1=".5" y1="3.5" x2="7.5" y2="3.5" stroke="currentColor"/></svg>Jan 23 2016</p></div>
    <p class="read-more">Read More News</p>
  </div>
</section>

<section class="wrap webinars">
  <h2 class="panel-head">Events and Webinars</h2>
  <div class="webinar-list">
    <article class="webinar">
      <div class="webinar-media coil" role="img" aria-label="Copper coil inductor on a circuit board"></div>
      <div><p class="webinar-title">Sed ut perspiciatis unde omnis iste na</p><p class="webinar-text">Sed ut perspiciatis unde omnis iste natus error sit voluptatem accu santi umolorem qb illo inventore veritatis et quasi archi-tecto beatae vitae dicta sunt explicabo. Nemo enim ipsam voluptatem</p><p class="news-date"><svg width="7" height="7" viewBox="0 0 8 8"><rect x=".5" y="1.5" width="7" height="6" fill="none" stroke="currentColor"/><line x1=".5" y1="3.5" x2="7.5" y2="3.5" stroke="currentColor"/></svg>Jan 23 2016</p></div>
    </article>
    <article class="webinar">
      <div class="webinar-media solar" role="img" aria-label="Solar panels under a bright sky"></div>
      <div><p class="webinar-title">Sed ut perspiciatis unde omnis iste na</p><p class="webinar-text">Sed ut perspiciatis unde omnis iste natus error sit voluptatem accu santi umolorem qb illo inventore veritatis et quasi archi-tecto beatae vitae dicta sunt explicabo. Nemo enim ipsam voluptatem</p><p class="news-date"><svg width="7" height="7" viewBox="0 0 8 8"><rect x=".5" y="1.5" width="7" height="6" fill="none" stroke="currentColor"/><line x1=".5" y1="3.5" x2="7.5" y2="3.5" stroke="currentColor"/></svg>Jan 23 2016</p></div>
    </article>
  </div>
</section>

<footer class="site-footer">
  <div class="social" aria-label="Social links"><span></span><span></span><span></span><span></span></div>
  <p class="copyright">© Copyright 2016 Vornimax A/S. All rights reserved.</p>
  <div class="footer-brand">Vornimax</div>
</footer>

</body>
</html>
```